New Business card design to reflect rebrand

I would like a business card design with a good base colour for our new logo and also a placeholder for a profile pic of the card holder. the design needs to be editable to the point that we can easily change the picture of the person and use that design for printmerlo etc. we are looking at a metalic finish business card so will need a good base colour to bring out the finish.

Target Market(s)

prospective customers

Industry/Entity Type

Business

Contact Information for Business Card

I would like one editable design that we can change the name of the card holder and profile picture. The design need to be in a format that be send to printmerlo etc.

Our address is Fenwick Lodge, Copse Lane, Ashford Vale, GU14 3TP Tel no. 01483 556172

Requirements
Must have
• place holder for a profile pic for the card holder. in AI or preferably PSD format

```html
<!DOCTYPE html>
<html lang="en">
<head>
<meta charset="utf-8">
<title>Corvane Workplace Services – Business Card</title>
<link href="https://fonts.googleapis.com/css2?family=Montserrat:wght@500;600;700&family=Open+Sans:wght@400;600&display=swap" rel="stylesheet">
<style>
  :root {
    --page: #e9e7e3;
    --card-white: #ffffff;
    --charcoal: #2a2a2c;
    --charcoal-light: #3a3a3d;
    --orange: #e8620f;
    --navy: #3f5877;
    --ink: #222222;
    --photo-a: #d7dbe1;
    --photo-b: #2b2f44;
  }
  * { box-sizing: border-box; margin: 0; padding: 0; }
  html, body { width: 1200px; height: 900px; overflow: hidden; background: var(--page); }
  .canvas { position: relative; width: 1200px; height: 900px; }

  .card {
    position: absolute;
    width: 640px;
    height: 366px;
    left: 280px;
    box-shadow: 0 6px 18px rgba(0,0,0,.18);
    overflow: hidden;
  }

  /* Back side – brand face */
  .card-back {
    top: 50px;
    background: linear-gradient(160deg, var(--charcoal-light) 0%, var(--charcoal) 55%, #1f1f21 100%);
    display: flex;
    flex-direction: column;
    align-items: center;
    justify-content: center;
    color: #ffffff;
    font-family: "Montserrat", sans-serif;
    font-weight: 600;
  }
  .brand-name { font-size: 64px; letter-spacing: 4px; line-height: 1; }
  .brand-tagline { font-size: 22px; letter-spacing: 9px; margin-top: 12px; }

  /* Front side – holder details */
  .card-front { top: 484px; background: var(--card-white); }
  .card-front svg.shapes { position: absolute; inset: 0; }

  .holder-name {
    position: absolute;
    left: 84px; top: 26px;
    font-family: "Montserrat", sans-serif;
    font-weight: 500;
    font-size: 24px;
    letter-spacing: 3px;
    text-transform: uppercase;
  }
  .holder-name .first { color: var(--orange); }
  .holder-name .last { color: var(--navy); }

  .contact {
    position: absolute;
    left: 40px; top: 106px;
    font-family: "Open Sans", sans-serif;
    font-size: 15px;
    line-height: 21px;
    color: var(--ink);
    list-style: none;
  }
  .contact li { display: flex; align-items: center; gap: 7px; }
  .contact svg { width: 11px; height: 11px; flex: none; }
  .contact .address { display: block; margin-top: 2px; }

  .profile-photo {
    position: absolute;
    left: 370px; top: 126px;
    width: 230px; height: 240px;
    background: linear-gradient(180deg, var(--photo-a) 0%, #9aa2b0 40%, var(--photo-b) 100%);
    border-radius: 115px 115px 0 0;
  }
</style>
</head>
<body>
<main class="canvas">

  <section class="card card-back" aria-label="Card back">
    <div class="brand-name">CORVANE</div>
    <div class="brand-tagline">WORKPLACE SERVICES</div>
  </section>

  <section class="card card-front" aria-label="Card front">
    <svg class="shapes" width="640" height="366" viewBox="0 0 640 366" aria-hidden="true">
      <polygon points="0,0 44,0 20,34 0,34" fill="var(--orange)"/>
      <polygon points="48,0 66,0 66,34 24,34" fill="var(--navy)"/>
      <polygon points="0,246 300,246 286,268 0,268" fill="var(--orange)"/>
      <polygon points="300,282 640,282 640,366 258,366" fill="var(--navy)"/>
    </svg>

    <h1 class="holder-name"><span class="first">Daniel</span> <span class="last">Hargreave</span></h1>

    <ul class="contact">
      <li>
        <svg viewBox="0 0 12 12"><path fill="var(--orange)" d="M2.5 1h2l1 2.6-1.3.9a6 6 0 0 0 3.3 3.3l.9-1.3 2.6 1v2a1.3 1.3 0 0 1-1.3 1.3A9.7 9.7 0 0 1 1.2 2.3 1.3 1.3 0 0 1 2.5 1z"/></svg>
        01483 556172
      </li>
      <li>
        <svg viewBox="0 0 12 12"><rect x="0.5" y="2" width="11" height="8" fill="var(--orange)"/><path d="M1 2.6 6 6.6l5-4" fill="none" stroke="#fff" stroke-width="1"/></svg>
        info@corvane.co.uk
      </li>
      <li class="address">Fenwick Lodge, Copse Lane,<br>Ashford Vale, GU14 3TP</li>
    </ul>

    <div class="profile-photo" role="img" aria-label="Profile photo of the card holder"></div>
  </section>

</main>
</body>
</html>
```